Business Card Design: recruitment/consultancy for business Thrive360onward

We need a business card design for a new company based in Adelaide Australia called Thrive360onward. Our Business aims to support people over 50 who may be looking for a career change, have been made redundant or generally looking for employment. We will also be working with businesses to provide them with recruiting solutions, job design, recruitment strategies and customised training. we will also be working with volunteering opportunities for those over 50.
We would like to see the E in thrive360onward strong and dominant. The final design should reflect change for the better, better opportunities, today is the day, make way for the new, all aimed at the 50 plus age group.
Colours we are thinking off include green (money, growth) black and white.... we like the idea of black and white photography with a one dominant colour...think of a of a black and white photo of a woman with dominant red lips...that sort of look

Business

Contact Information for Business Card

Kim, Mavis & Gwen
phone: 0439615028
Thrive360onward@mailbox-example.net
Facebook/Thrive360onward
www.thrive360onward-example.com.au

```html
<!DOCTYPE html>
<html lang="en">
<head>
<meta charset="utf-8">
<title>Thrive360onward – Business Card</title>
<link rel="stylesheet" href="https://fonts.googleapis.com/css2?family=Pinyon+Script&display=swap">
<style>
  :root {
    --stage: #ece9e4;
    --card-black: #0b0b0b;
    --ink-white: #f4f4f4;
    --ink-black: #161616;
    --accent-red: #d7192a;
    --photo-dark: #5a5a5a;
    --photo-mid: #a9a9a9;
    --photo-light: #e6e6e6;
    --rule: #e8e8e8;
  }
  * { box-sizing: border-box; margin: 0; padding: 0; }
  html, body {
    width: 1200px; height: 886px; overflow: hidden;
    background: var(--stage);
  }
  .sheet {
    width: 1200px; height: 886px;
    display: flex; align-items: center; justify-content: center; gap: 30px;
  }
  .card {
    position: relative;
    width: 560px; height: 320px;
    border-radius: 14px;
    overflow: hidden;
    box-shadow: 0 6px 18px rgba(0,0,0,.18);
    font-family: "Pinyon Script", cursive;
  }

  /* Brand name with red accent dot */
  .wordmark {
    position: absolute;
    display: flex; align-items: center; gap: 12px;
    font-size: 58px; line-height: 1; white-space: nowrap; font-weight: 400;
  }
  .wordmark__dot {
    width: 16px; height: 16px; border-radius: 50%;
    background: var(--accent-red); flex: none;
  }

  /* Contact side */
  .card--contact { background: var(--card-black); color: var(--ink-white); }
  .card--contact .wordmark { left: 36px; top: 70px; color: var(--ink-white); }
  .divider {
    position: absolute; left: 0; right: 0; top: 150px; height: 36px;
    display: flex; align-items: center; gap: 14px;
  }
  .divider__line { height: 2px; background: var(--rule); }
  .divider__line--long { flex: 1; }
  .divider__line--short { width: 34px; }
  .partners { font-size: 26px; white-space: nowrap; line-height: 36px; }
  .contact-list {
    position: absolute; left: 226px; top: 204px;
    list-style: none; font-size: 18px; line-height: 25px;
  }

  /* Photo side */
  .card--photo { background: var(--photo-light); }
  .photo-area {
    position: absolute; inset: 0;
    background:
      radial-gradient(circle at 78% 30%, rgba(255,255,255,.55) 0 60px, transparent 61px),
      radial-gradient(circle at 62% 70%, rgba(255,255,255,.35) 0 45px, transparent 46px),
      linear-gradient(100deg, var(--photo-dark) 0%, var(--photo-mid) 45%, var(--photo-light) 80%);
  }
  .card--photo .wordmark {
    right: 28px; top: 128px; color: var(--ink-black); font-size: 52px;
  }
</style>
</head>
<body>
<main class="sheet">
  <section class="card card--contact" aria-label="Business card contact side">
    <h1 class="wordmark"><span class="wordmark__dot" aria-hidden="true"></span>thrive360onward</h1>
    <div class="divider">
      <span class="divider__line divider__line--long"></span>
      <span class="partners">Kim, Mavis &amp; Gwen</span>
      <span class="divider__line divider__line--short"></span>
    </div>
    <ul class="contact-list">
      <li>0439615028</li>
      <li>Thrive360onward@mailbox-example.net</li>
      <li>Facebook/Thrive360onward</li>
      <li>www.thrive360onward-example.com.au</li>
    </ul>
  </section>

  <section class="card card--photo" aria-label="Business card photo side">
    <div class="photo-area" role="img" aria-label="Black and white photograph of three smiling older women with soft light bokeh"></div>
    <p class="wordmark"><span class="wordmark__dot" aria-hidden="true"></span>thrive360onward</p>
  </section>
</main>
</body>
</html>
```